Quorva - corporate Business Card

We need a good look and innovative business card for a new start up company based in Los Angeles called "Quorva". We are in a payment business, including payment card, app, and ewallet. We are expert in online payment and Card not present (CNP) transaction.
We need an innovative, modern business card.

Our logo font is Aero Matics

Target Market(s)

Startup - Bank - Online Payment - Card Manufacturing

Industry/Entity Type

Startup

Contact Information for Business Card

phone: 555 014 7396 - Address: 4172 Marlowe blvd, Ashvale City, CA 90299

Requirements
Must have
• Message: innovative, professional, expert, high tech, trust, online payment expert, security
Nice to have
• no comment
Should not have
• no Comment

```html
<!DOCTYPE html>
<html lang="en">
<head>
<meta charset="utf-8">
<title>Quorva — Business Card</title>
<link href="https://fonts.googleapis.com/css2?family=Source+Sans+3:wght@400;600&display=swap" rel="stylesheet">
<style>
  :root{
    --brand-red:#b51f2e;
    --accent-gray:#8a8a8a;
    --paper:#ffffff;
    --ink-gray:#5c5c5c;
    --backdrop:#e8e5e1;
  }
  *{margin:0;padding:0;box-sizing:border-box}
  html,body{width:1200px;height:987px;overflow:hidden}
  body{background:var(--backdrop);font-family:"Source Sans 3",sans-serif;position:relative}

  .card{position:absolute;left:293px;width:615px;height:351px;overflow:hidden;box-shadow:0 2px 6px rgba(0,0,0,.18)}
  .card--front{top:130px;background:var(--paper)}
  .card--back{top:506px;background:var(--brand-red)}

  /* front */
  .brand{position:absolute;left:33px;top:46px;display:flex;align-items:center;gap:12px}
  .brand__dot{width:76px;height:76px;border-radius:50%;background:var(--brand-red);flex:none}
  .brand__name{font-size:54px;font-weight:600;color:var(--brand-red);line-height:1;letter-spacing:.5px}

  .person{position:absolute;right:37px;top:54px;text-align:right}
  .person__name{font-size:22px;font-weight:600;color:var(--brand-red);letter-spacing:.4px;line-height:1.1}
  .person__role{font-size:17px;color:var(--ink-gray);line-height:1.3}

  .contact-band{position:absolute;left:0;top:180px;width:100%;height:149px;background:var(--brand-red)}
  .contact-band__side{position:absolute;right:0;top:0;width:105px;height:100%;background:var(--accent-gray)}
  .contact-band__disc{position:absolute;left:415px;top:-3px;width:154px;height:154px;border-radius:50%;background:var(--paper)}

  .contact{position:absolute;left:32px;top:12px;color:#fff;font-size:16px;line-height:23px}
  .contact__address{margin-bottom:8px}
  .contact__row{display:flex;align-items:center;gap:9px}
  .contact__row svg{width:15px;height:15px;flex:none;margin-left:2px}

  /* back */
  .brand--back{left:116px;top:117px;gap:14px}
  .brand--back .brand__dot{width:115px;height:115px;background:var(--paper)}
  .brand--back .brand__name{font-size:78px;color:#fff;font-weight:400}
  .back-url{position:absolute;left:0;right:0;top:292px;text-align:center;color:#fff;font-size:15px;letter-spacing:7px}
</style>
</head>
<body>

<section class="card card--front">
  <div class="brand">
    <span class="brand__dot"></span>
    <span class="brand__name">Quorva</span>
  </div>

  <div class="person">
    <div class="person__name">OWEN PARKS</div>
    <div class="person__role">CEO&amp;Founder</div>
  </div>

  <div class="contact-band">
    <div class="contact-band__side"></div>
    <div class="contact-band__disc"></div>

    <div class="contact">
      <div class="contact__address">4172 Marlowe blvd<br>Ashvale City, CA 90299</div>
      <div class="contact__row">
        <svg viewBox="0 0 16 16" aria-hidden="true"><path fill="#fff" d="M3.6 1.2l2.3 2.5-1.3 1.8c.9 2 2.3 3.5 4.3 4.5l1.8-1.3 2.5 2.3-1.3 2.5C7.3 13.6 2.4 8.7 1.1 2.5z"/></svg>
        <span>555 014 7396</span>
      </div>
      <div class="contact__row">
        <svg viewBox="0 0 16 16" aria-hidden="true"><rect x="1.5" y="3.5" width="13" height="9" fill="none" stroke="#fff" stroke-width="1.6"/><path d="M1.5 3.5l6.5 5 6.5-5" fill="none" stroke="#fff" stroke-width="1.6"/></svg>
        <span>owen@quorva.com</span>
      </div>
      <div class="contact__row">
        <svg viewBox="0 0 16 16" aria-hidden="true"><circle cx="8" cy="8" r="6.6" fill="#fff"/><path d="M4.5 5.5c1.5 0 2 1 1.5 2s1 1.5 1 2.8M9.5 3c.5 1.2 1.8 1.5 2.5 2.8-.8.8-2 .6-2.3 1.8" fill="none" stroke="#b51f2e" stroke-width="1.2"/></svg>
        <span>www.quorva.com</span>
      </div>
    </div>
  </div>
</section>

<section class="card card--back">
  <div class="brand brand--back">
    <span class="brand__dot"></span>
    <span class="brand__name">Quorva</span>
  </div>
  <div class="back-url">www.quorva.com</div>
</section>

</body>
</html>
```